PlayTallyCollective - Game Statistics and Achievement Tracking

I need a new modern design for an existing website.

The website is a project to track statistics and achievements for games (currently Vaporn Achievements/Stats and stats for Cargo Haul Odyssey 2 and Frontier Rig Journeys).
I am currently expanding the site with other platforms (like QVR) and more games.
I am also adding a user registration/signin with user profiles to show off their achievements and stats across all platforms and games.

The current website is available at https://plytly.example/
To search for data you can use the username "pixelornin" (without quotes).

The design should be modern and extendable and contain space for a logo.

The logo should match the project. It should combine Gaming with statistics.

Target Market(s)

Video game players

Number of Pages Required

5+ page

Font styles to use
Sans Serif

Requirements
Must have
• Basic Layout, User profile page (not yet available on live site), Search Page for Platforms/Games, Platform profile page, Dark theme

```html
<!DOCTYPE html>
<html lang="en">
<head>
<meta charset="utf-8">
<title>PlayTallyCollective</title>
<link href="https://fonts.googleapis.com/css2?family=Silkscreen:wght@400;700&family=Montserrat:wght@400;500;600;700&display=swap" rel="stylesheet">
<style>
:root{
  --bg:#050208;
  --ink:#ffffff;
  --muted:#d8d3e6;
  --violet:#5b3cf5;
  --violet-deep:#3a1fb8;
  --magenta:#f012d6;
  --pink:#ff2bd8;
  --tile-bar:#3d3942;
  --card:#1a0a24;
}
*{margin:0;padding:0;box-sizing:border-box}
html,body{width:1200px;height:3317px;overflow:hidden}
body{
  position:relative;background:var(--bg);color:var(--ink);
  font-family:"Montserrat",sans-serif;
  background:
    radial-gradient(ellipse 520px 420px at 1130px 180px,rgba(170,20,190,.55),transparent 70%),
    radial-gradient(ellipse 560px 420px at 240px 560px,rgba(60,40,170,.55),transparent 70%),
    radial-gradient(ellipse 420px 380px at 1120px 1120px,rgba(180,20,170,.5),transparent 70%),
    radial-gradient(ellipse 520px 420px at 180px 1600px,rgba(110,30,190,.45),transparent 70%),
    radial-gradient(ellipse 420px 420px at 1150px 1600px,rgba(160,20,170,.45),transparent 70%),
    radial-gradient(ellipse 440px 420px at 80px 2500px,rgba(70,40,180,.5),transparent 70%),
    radial-gradient(ellipse 440px 420px at 1150px 2500px,rgba(170,20,170,.45),transparent 70%),
    radial-gradient(ellipse 620px 380px at 1150px 3250px,rgba(180,30,200,.6),transparent 70%),
    radial-gradient(ellipse 520px 380px at 100px 3250px,rgba(80,40,200,.45),transparent 70%),
    var(--bg);
}
.abs{position:absolute}
.pixel{font-family:"Silkscreen",monospace;font-weight:700;letter-spacing:.18em}

/* header */
.brand{display:flex;align-items:center;gap:12px}
.brand-mark{width:18px;height:18px;background:var(--magenta)}
.brand-name{font-family:"Montserrat",sans-serif;font-weight:700;font-size:24px;color:var(--ink);letter-spacing:.02em}
.nav{display:flex;gap:0;font-size:15px;font-weight:500}
.nav a{color:var(--ink);text-decoration:none;position:absolute;top:56px}
.nav a.active{color:var(--pink);text-decoration:underline}
.btn{position:absolute;display:flex;align-items:center;justify-content:center;font-weight:700;color:#fff;font-size:16px;
  clip-path:polygon(0 0,86% 0,100% 30%,100% 100%,14% 100%,0 70%)}
.btn-violet{background:linear-gradient(90deg,var(--violet),#6a3cf0)}
.btn-pink{background:var(--magenta)}
.btn-grad{background:linear-gradient(90deg,var(--violet) 0%,#8a2be2 55%,var(--magenta) 100%)}

/* hero */
.center{left:0;width:1200px;text-align:center}
.hero-kicker{top:203px;font-size:36px;color:var(--pink)}
.hero-title{top:266px;font-size:44px}
.hero-copy{top:346px;font-size:18px;font-weight:500;line-height:35px}

/* profile */
.profile{left:110px;top:637px;width:981px;height:409px}
.avatar{left:193px;top:701px;width:261px;height:271px;border-radius:4px;
  background:radial-gradient(circle at 50% 45%,#6bd8ff,#1f74c9 60%,#0c2a6b);box-shadow:0 0 22px #1ab0ff}
.stats-list{left:512px;top:709px;font-size:16px;font-weight:700}
.stats-list .row{display:flex;height:45.5px}
.stats-list .label{width:197px}
.profile-icons{left:918px;top:995px;display:flex;gap:18px}

/* headings */
.section-title{font-size:50px}

/* search */
.search{left:164px;top:1214px;width:872px;height:62px;border-radius:31px;border:2px solid #7a3cf0;
  background:#141018;display:flex;align-items:center;justify-content:space-between;padding:0 28px;font-size:16px}

/* games */
.tile{position:absolute;width:220px}
.tile-cover{height:85px}
.tile-meta{height:50px;background:var(--tile-bar);display:flex;justify-content:space-between;align-items:center;padding:0 34px 0 38px;font-size:15px}
.tile-progress{height:35px;background:var(--violet);display:flex;align-items:center;justify-content:center;font-size:15px;font-weight:700}

/* statistics */
.stat{position:absolute;text-align:center;width:300px}
.stat-num{font-size:54px;font-weight:700;line-height:1}
.stat-label{font-family:"Silkscreen",monospace;font-weight:700;letter-spacing:.2em;font-size:22px;line-height:36px;margin-top:14px}
.divider{position:absolute;width:2px;height:220px;background:linear-gradient(var(--magenta),#ff3ae0,var(--magenta));top:2045px}
.divider::after{content:"";position:absolute;left:-9px;top:103px;width:20px;height:20px;border-radius:50%;background:var(--pink);box-shadow:0 0 14px var(--pink)}

/* users */
.user{position:absolute;top:2504px;width:271px;height:366px}
.user-name{position:absolute;left:0;width:100%;top:320px;text-align:center;font-size:17px;font-weight:600}

/* footer */
.footer-nav{top:3156px;font-size:24px;font-weight:600}
.footer-nav span{margin:0 30px}
.copyright{top:3242px;font-size:17px;font-weight:600}
</style>
</head>
<body>

<!-- header -->
<header>
  <div class="abs brand" style="left:50px;top:56px">
    <span class="brand-mark"></span>
    <span class="brand-name">PlayTallyCollective</span>
  </div>
  <nav class="nav">
    <a class="active" href="#" style="left:479px">HOME</a>
    <a href="#" style="left:570px">ABOUT US</a>
    <a href="#" style="left:693px">VAPORN</a>
    <a href="#" style="left:791px">GAME</a>
  </nav>
  <a class="btn btn-violet" style="left:879px;top:40px;width:141px;height:52px">REGISTER</a>
  <a class="btn btn-pink" style="left:1041px;top:40px;width:108px;height:52px">LOGIN</a>
</header>

<!-- hero -->
<section>
  <div class="abs center pixel hero-kicker">WELCOME TO</div>
  <h1 class="abs center pixel hero-title">PLAYTALLYCOLLECTIVE</h1>
  <p class="abs center hero-copy">Lorem ipsum dolor sit amet, consectetur adipiscing elit, sed do eiusmod<br>tempor incididunt ut labore et dolore magna aliqua.</p>
  <a class="btn btn-grad" style="left:513px;top:453px;width:175px;height:51px;font-size:16px">GET STARTED</a>
</section>

<!-- profile card -->
<section>
  <svg class="abs profile" viewBox="0 0 981 409">
    <defs>
      <linearGradient id="cardStroke" x1="0" y1="1" x2="1" y2="0">
        <stop offset="0" stop-color="#5b3cf5"/><stop offset="1" stop-color="#f012d6"/>
      </linearGradient>
      <linearGradient id="cardFill" x1="0" y1="0" x2="1" y2="1">
        <stop offset="0" stop-color="#1b0b36"/><stop offset="1" stop-color="#300a36"/>
      </linearGradient>
    </defs>
    <polygon points="1,1 849,1 980,172 980,408 128,408 1,238" fill="url(#cardFill)" stroke="url(#cardStroke)" stroke-width="2.5"/>
  </svg>
  <div class="abs avatar" role="img" aria-label="Player avatar illustration"></div>
  <div class="abs stats-list">
    <div class="row"><span class="label">PLAYED GAMES:</span><span>1166/1644 (70%)</span></div>
    <div class="row"><span class="label">TOTAL PLAY TIME:</span><span>1 year 2 months 11 hours 25 minutes</span></div>
    <div class="row"><span class="label">ACHIEVEMENTS:</span><span>18007/63070 (28%)</span></div>
    <div class="row"><span class="label">MEMBER SINCE:</span><span>14.01.2009</span></div>
    <div class="row"><span class="label">LAST PLAYED:</span><span>Rail Route Sim 5</span></div>
    <div class="row"><span class="label">LAST UPDATE:</span><span>26.12.2024 16:00h</span></div>
  </div>
  <div class="abs profile-icons">
    <svg width="20" height="20" viewBox="0 0 20 20" fill="none" stroke="#fff" stroke-width="1.8"><path d="M16 10a6 6 0 1 1-2-4.5"/><path d="M14 2v4h-4"/></svg>
    <svg width="20" height="20" viewBox="0 0 20 20" fill="none" stroke="#fff" stroke-width="1.6"><rect x="3" y="4" width="14" height="13" rx="1.5"/><path d="M3 8h14M7 2v4M13 2v4"/></svg>
    <svg width="20" height="20" viewBox="0 0 20 20"><circle cx="10" cy="10" r="8" fill="#5fb8f0"/></svg>
    <svg width="20" height="20" viewBox="0 0 20 20" fill="none" stroke="#fff" stroke-width="1.6"><ellipse cx="10" cy="4.5" rx="7" ry="2.5"/><path d="M3 4.5v11c0 1.4 3.1 2.5 7 2.5s7-1.1 7-2.5v-11M3 8.2c0 1.4 3.1 2.5 7 2.5s7-1.1 7-2.5M3 12c0 1.4 3.1 2.5 7 2.5s7-1.1 7-2.5"/></svg>
  </div>
</section>

<!-- games -->
<section>
  <h2 class="abs center pixel section-title" style="top:1120px">OUR GAMES</h2>
  <div class="abs search"><span>Search</span>
    <svg width="14" height="14" viewBox="0 0 14 14" fill="none" stroke="#fff" stroke-width="2"><circle cx="6" cy="6" r="4.3"/><path d="M9.3 9.3 13 13"/></svg>
  </div>

  <div class="tile" style="left:111px;top:1337px"><div class="tile-cover" role="img" aria-label="Game cover art" style="background:linear-gradient(120deg,#d8c7b0,#5a4a3a 60%,#2b3a70)"></div><div class="tile-meta"><span>5h</span><span>1 / 1</span></div><div class="tile-progress">100%</div></div>
  <div class="tile" style="left:363px;top:1337px"><div class="tile-cover" role="img" aria-label="Game cover art" style="background:linear-gradient(120deg,#0a0505,#3a1010 60%,#120808)"></div><div class="tile-meta"><span>2h</span><span>1 / 1</span></div><div class="tile-progress">100%</div></div>
  <div class="tile" style="left:616px;top:1337px"><div class="tile-cover" role="img" aria-label="Game cover art" style="background:linear-gradient(120deg,#3a6cd8,#8a4be0 55%,#3bc6e0)"></div><div class="tile-meta"><span>27h</span><span>5 / 5</span></div><div class="tile-progress">100%</div></div>
  <div class="tile" style="left:868px;top:1337px"><div class="tile-cover" role="img" aria-label="Game cover art" style="background:linear-gradient(120deg,#2a3848,#5a6878 50%,#1a1a22)"></div><div class="tile-meta"><span>36h</span><span>6 / 6</span></div><div class="tile-progress">100%</div></div>

  <div class="tile" style="left:111px;top:1543px"><div class="tile-cover" role="img" aria-label="Game cover art" style="background:linear-gradient(120deg,#6a6a6a,#2a2a2a 50%,#5a8ad0)"></div><div class="tile-meta"><span>2h</span><span>8 / 8</span></div><div class="tile-progress">100%</div></div>
  <div class="tile" style="left:363px;top:1543px"><div class="tile-cover" role="img" aria-label="Game cover art" style="background:linear-gradient(120deg,#7ae0d8,#bff0f0 50%,#4cc6c0)"></div><div class="tile-meta"><span>2h</span><span>8 / 8</span></div><div class="tile-progress">100%</div></div>
  <div class="tile" style="left:616px;top:1543px"><div class="tile-cover" role="img" aria-label="Game cover art" style="background:linear-gradient(120deg,#8ac850,#d8d070 50%,#5a9a3a)"></div><div class="tile-meta"><span>59h</span><span>6 / 6</span></div><div class="tile-progress">100%</div></div>
  <div class="tile" style="left:868px;top:1543px"><div class="tile-cover" role="img" aria-label="Game cover art" style="background:linear-gradient(120deg,#3a1a2a,#8a3048 50%,#2a1a3a)"></div><div class="tile-meta"><span>43h</span><span>6 / 6</span></div><div class="tile-progress">100%</div></div>

  <a class="btn btn-grad" style="left:513px;top:1785px;width:175px;height:51px">VIEW MORE</a>
</section>

<!-- statistics -->
<section>
  <h2 class="abs center pixel section-title" style="top:1910px">OUR STATISTICS</h2>
  <svg class="abs" style="left:43px;top:2163px" width="20" height="30" viewBox="0 0 20 30" fill="none" stroke="#bbb" stroke-width="3"><path d="M15 3 4 15l11 12"/></svg>
  <svg class="abs" style="left:1128px;top:2163px" width="20" height="30" viewBox="0 0 20 30" fill="none" stroke="#fff" stroke-width="3"><path d="M5 3l11 12L5 27"/></svg>

  <svg class="abs" style="left:212px;top:2062px" width="84" height="64" viewBox="0 0 84 64"><path d="M20 4h44c10 0 18 10 20 30s-4 30-12 28c-6-1-10-12-16-14H28c-6 2-10 13-16 14-8 2-14-8-12-28S10 4 20 4z" fill="#ff2bd8"/><path d="M22 22v16M14 30h16" stroke="#2a0520" stroke-width="5"/><circle cx="58" cy="24" r="4" fill="#2a0520"/><circle cx="66" cy="34" r="4" fill="#2a0520"/></svg>
  <div class="stat" style="left:102px;top:2148px"><div class="stat-num">251966</div><div class="stat-label">GAMES</div></div>

  <div class="divider" style="left:421px"></div>

  <svg class="abs" style="left:566px;top:2046px" width="72" height="70" viewBox="0 0 72 70"><path d="M14 2h44v20c0 14-10 24-22 24S14 36 14 22z" fill="#ff2bd8"/><path d="M14 8H4c0 12 6 18 12 18M58 8h10c0 12-6 18-12 18" stroke="#ff2bd8" stroke-width="5" fill="none"/><rect x="31" y="44" width="10" height="12" fill="#ff2bd8"/><rect x="20" y="56" width="32" height="12" fill="#ff2bd8"/></svg>
  <div class="stat" style="left:452px;top:2137px"><div class="stat-num">2692707</div><div class="stat-label">GAMES<br>ACHIEVEMENTS</div></div>

  <div class="divider" style="left:789px"></div>

  <svg class="abs" style="left:912px;top:2048px" width="78" height="78" viewBox="0 0 78 78"><rect x="2" y="50" width="12" height="26" fill="#ff2bd8"/><rect x="20" y="40" width="12" height="36" fill="#ff2bd8"/><rect x="38" y="54" width="12" height="22" fill="#ff2bd8"/><rect x="56" y="28" width="12" height="48" fill="#ff2bd8"/><path d="M6 36 26 22l18 14L70 8" stroke="#ff2bd8" stroke-width="5" fill="none"/><circle cx="70" cy="8" r="6" fill="#ff2bd8"/></svg>
  <div class="stat" style="left:808px;top:2148px"><div class="stat-num">339284</div><div class="stat-label">GAME STATS</div></div>
</section>

<!-- users -->
<section>
  <h2 class="abs center pixel section-title" style="top:2383px">OUR USERS</h2>
  <svg class="abs" style="left:43px;top:2690px" width="20" height="30" viewBox="0 0 20 30" fill="none" stroke="#bbb" stroke-width="3"><path d="M15 3 4 15l11 12"/></svg>
  <svg class="abs" style="left:1128px;top:2690px" width="20" height="30" viewBox="0 0 20 30" fill="none" stroke="#fff" stroke-width="3"><path d="M5 3l11 12L5 27"/></svg>

  <svg width="0" height="0" style="position:absolute">
    <defs>
      <linearGradient id="userStroke" x1="0" y1="0" x2="1" y2="1"><stop offset="0" stop-color="#7a3cf0"/><stop offset="1" stop-color="#f012d6"/></linearGradient>
      <linearGradient id="photoA" x1="0" y1="0" x2="1" y2="1"><stop offset="0" stop-color="#e0508a"/><stop offset=".5" stop-color="#a36ad0"/><stop offset="1" stop-color="#3a3aa0"/></linearGradient>
      <linearGradient id="photoB" x1="0" y1="0" x2="1" y2="1"><stop offset="0" stop-color="#5a4ad0"/><stop offset=".5" stop-color="#c08a7a"/><stop offset="1" stop-color="#3a4a8a"/></linearGradient>
      <linearGradient id="photoC" x1="0" y1="0" x2="1" y2="1"><stop offset="0" stop-color="#c040b0"/><stop offset=".5" stop-color="#6a3aa0"/><stop offset="1" stop-color="#2a2a70"/></linearGradient>
    </defs>
  </svg>

  <div class="user" style="left:112px">
    <svg width="271" height="366" viewBox="0 0 271 366"><polygon points="1,1 236,1 270,88 270,365 40,365 1,240" fill="#1d0a28" stroke="url(#userStroke)" stroke-width="2"/><polygon role="img" aria-label="Portrait photo of a player" points="11,13 228,13 258,92 258,296 11,296" fill="url(#photoA)"/></svg>
    <div class="user-name">LOREM IPSUM</div>
  </div>
  <div class="user" style="left:466px">
    <svg width="271" height="366" viewBox="0 0 271 366"><polygon points="1,1 236,1 270,88 270,365 40,365 1,240" fill="#1d0a28" stroke="url(#userStroke)" stroke-width="2"/><polygon role="img" aria-label="Portrait photo of a player" points="11,13 228,13 258,92 258,296 11,296" fill="url(#photoB)"/></svg>
    <div class="user-name">LOREM IPSUM</div>
  </div>
  <div class="user" style="left:820px">
    <svg width="271" height="366" viewBox="0 0 271 366"><polygon points="1,1 236,1 270,88 270,365 40,365 1,240" fill="#1d0a28" stroke="url(#userStroke)" stroke-width="2"/><polygon role="img" aria-label="Portrait photo of a player" points="11,13 228,13 258,92 258,296 11,296" fill="url(#photoC)"/></svg>
    <div class="user-name">LOREM IPSUM</div>
  </div>
</section>

<!-- footer -->
<footer>
  <div class="abs brand" style="left:0;width:1200px;justify-content:center;top:3040px">
    <span class="brand-mark" style="width:24px;height:24px"></span>
    <span class="brand-name" style="font-size:38px">PlayTallyCollective</span>
  </div>
  <div class="abs center footer-nav"><span>HOME</span><span>ABOUT US</span><span>VAPORN</span><span>GAME</span><span>CONTACT US</span></div>
  <div class="abs center copyright">COPYRIGHTS@2024.PLAYTALLYCOLLECTIVE.ALL RIGHTS RESERVED</div>
</footer>

</body>
</html>
```